Business Card Design for Training Business

Clear Path Coaching is a new business that delivers training and other services with a focus on topics related to mental health and wellbeing, for example, Wellmind Response Course, Resilience etc. We have a strong focus on evidence-based psychology and neuroscience. I have a logo which I will upload with the brief, so please consider colours that work well with the logo.
Target Market(s)
Adults, workplaces (particularly government and not-for-profits)
Industry/Entity Type
Business
Contact Information for Business Card
Head Strong TrainingSamantha SellwoodDirector0438 770 850sam@headstrongtraining.com.auwww.headstrongtraining.com.au

```html
<!DOCTYPE html>
<html lang="en">
<head>
<meta charset="utf-8">
<title>Clear Path Coaching – Business Card</title>
<link rel="stylesheet" href="https://fonts.googleapis.com/css2?family=Arimo:wght@400;700&display=swap">
<style>
  :root {
    --backdrop: #e9e6e2;
    --card-black: #000000;
    --card-light: #f2f2f2;
    --card-mid: #dcdcdc;
    --ink: #111111;
    --brand-grey: #5c5c5c;
    --icon-fill: #1a1a1a;
    --icon-mark: #ffffff;
  }
  * { box-sizing: border-box; margin: 0; padding: 0; }
  html, body {
    width: 1200px;
    height: 960px;
    overflow: hidden;
    background: var(--backdrop);
  }
  .card {
    position: absolute;
    left: 120px;
    top: 190px;
    width: 960px;
    height: 580px;
    overflow: hidden;
    font-family: "Arimo", Arial, sans-serif;
    color: var(--ink);
    box-shadow: 0 6px 18px rgba(0,0,0,0.18);
  }
  .card__texture {
    position: absolute;
    inset: 0;
    background: linear-gradient(135deg, var(--card-light) 0%, #e6e6e6 45%, var(--card-light) 65%, var(--card-mid) 100%);
  }
  .card__panel {
    position: absolute;
    left: 0;
    top: 0;
    width: 960px;
    height: 580px;
  }
  .card__panel path { fill: var(--card-black); }
  .brand {
    position: absolute;
    left: 30px;
    top: 330px;
    width: 420px;
    text-align: center;
    font-weight: 400;
    color: var(--brand-grey);
    text-transform: uppercase;
    letter-spacing: 4px;
    font-size: 38px;
    line-height: 1.2;
  }
  .person {
    position: absolute;
    right: 80px;
    top: 100px;
    text-align: right;
  }
  .person__name {
    font-size: 36px;
    font-weight: 700;
    letter-spacing: -0.5px;
  }
  .person__role {
    font-size: 20px;
    font-weight: 700;
    margin-top: 4px;
  }
  .contacts {
    position: absolute;
    right: 40px;
    top: 330px;
    list-style: none;
    text-align: right;
  }
  .contacts__item {
    display: flex;
    justify-content: flex-end;
    align-items: center;
    gap: 12px;
    font-size: 18px;
    font-weight: 700;
    letter-spacing: -0.2px;
    height: 38px;
  }
  .contacts__icon {
    width: 18px;
    height: 18px;
    flex: none;
  }
  .contacts__icon rect { fill: var(--icon-fill); }
  .contacts__icon .mark { fill: none; stroke: var(--icon-mark); stroke-width: 1.4; }
  .contacts__icon .mark-solid { fill: var(--icon-mark); }
</style>
</head>
<body>
  <main class="card">
    <div class="card__texture" role="img" aria-label="Light grey faceted polygon background pattern"></div>
    <svg class="card__panel" viewBox="0 0 960 580" aria-hidden="true">
      <path d="M0,0 L420,0 Q600,300 450,580 L0,580 Z"/>
    </svg>

    <div class="brand">Clear Path<br>Coaching</div>

    <div class="person">
      <p class="person__name">Rebecca Tanfield</p>
      <p class="person__role">Director</p>
    </div>

    <ul class="contacts">
      <li class="contacts__item">
        <span>0491 362 517</span>
        <svg class="contacts__icon" viewBox="0 0 18 18" aria-hidden="true">
          <rect width="18" height="18" rx="2"/>
          <path class="mark-solid" d="M5,4 L7,4 L8,7 L7,8 Q8,10.5 10,11 L11,10 L14,11 L14,13 Q13,14 11,14 Q5,12 4,6 Q4,4.5 5,4 Z"/>
        </svg>
      </li>
      <li class="contacts__item">
        <span>bec@clearpathcoaching.example.au</span>
        <svg class="contacts__icon" viewBox="0 0 18 18" aria-hidden="true">
          <rect width="18" height="18" rx="2"/>
          <rect class="mark" x="3.5" y="5" width="11" height="8" style="fill:none"/>
          <path class="mark" d="M3.5,5 L9,9.5 L14.5,5"/>
        </svg>
      </li>
      <li class="contacts__item">
        <span>www.clearpathcoaching.example.au</span>
        <svg class="contacts__icon" viewBox="0 0 18 18" aria-hidden="true">
          <rect width="18" height="18" rx="2"/>
          <circle class="mark" cx="9" cy="9" r="5"/>
          <ellipse class="mark" cx="9" cy="9" rx="2.2" ry="5"/>
          <path class="mark" d="M4,9 L14,9"/>
        </svg>
      </li>
    </ul>
  </main>
</body>
</html>
```